New web design for a service provider in the medical field

We are looking for a new design for our website. We are a company that repairs and sells medical endoscopes. Our customers include doctors and hospitals. Our current website can be found at https://lumavex.de/en/lumavex-english.
We need a new web design (without programming) for the following 3 pages:
-Startpage https://lumavex.de/en/lumavex-english/
-Used endoscopes https://lumavex.de/en/used-endoscopes/
-Purchase https://lumavex.de/en/purchase/
The design should be modern and stylish.
The blue color of the logo should be reflected on the page, but not too intrusive.
I have uploaded the images from the header. If more images are needed, let me know and I will upload them.

Target Market(s)
Doctors and hospitals

```html
<!DOCTYPE html>
<html lang="en">
<head>
<meta charset="utf-8">
<title>Lumavex – Endoscope Repair</title>
<link rel="stylesheet" href="https://fonts.googleapis.com/css2?family=Exo+2:wght@500;600;700&family=Montserrat:wght@400;500;600;700&display=swap">
<style>
:root{
  --blue:#0a74c1;
  --blue-dark:#0353a4;
  --nav:#09aaea;
  --pale:#e5eff8;
  --ink:#2e3b4a;
  --text:#4a5563;
  --white:#fff;
}
*{box-sizing:border-box;margin:0;padding:0}
html,body{width:1200px;height:4615px;overflow:hidden}
body{position:relative;background:var(--white);font-family:"Montserrat",sans-serif;color:var(--text)}
.abs{position:absolute}
h1,h2,h3,.display{font-family:"Exo 2",sans-serif}
.btn{position:absolute;display:flex;align-items:center;justify-content:center;background:var(--blue-dark);color:var(--white);border-radius:30px;font-size:17px;font-weight:600;text-transform:uppercase;text-decoration:none}

/* header */
.brand{position:absolute;display:flex;align-items:center;gap:12px;text-decoration:none}
.brand-dot{width:22px;height:22px;border-radius:50%;background:var(--nav)}
.brand-name{font-family:"Montserrat",sans-serif;font-weight:700;color:var(--blue-dark)}
.toplinks{left:765px;top:29px;font-size:13px;color:#6a7380;letter-spacing:.2px}
.toplinks b{color:var(--blue-dark)}
.contact{display:flex;align-items:center;gap:14px;font-size:18px;font-weight:500;color:var(--blue-dark)}
.icircle{width:34px;height:34px;border-radius:50%;background:#24405e;display:flex;align-items:center;justify-content:center}
.nav{left:0;top:131px;width:1200px;height:59px;background:var(--nav);display:flex;align-items:center}
.nav a{position:absolute;color:var(--white);font-size:14px;font-weight:500;text-decoration:none;text-transform:uppercase}

/* hero */
.hero{left:0;top:190px;width:1200px;height:652px;background:linear-gradient(120deg,#b9c3cf 0%,#8d9bab 45%,#4a5e7e 70%,#2d4a8a 100%)}
.hero-title{left:75px;top:345px;font-size:72px;font-weight:600;color:var(--white);letter-spacing:1px}
.hero-sub{left:75px;top:432px;font-size:36px;font-weight:600;color:var(--white);line-height:42px}
.hero-inset{left:525px;top:439px;width:270px;height:270px;border-radius:50%;border:6px solid var(--white);background:linear-gradient(140deg,#a8b4c2,#4c5c72)}

/* service cards */
.svc{position:absolute;color:var(--white);border-radius:22px;padding:26px 22px}
.svc h3{font-size:24px;font-weight:600;margin-top:8px}
.svc h4{font-size:19px;font-weight:600;font-family:"Exo 2",sans-serif;margin-top:2px}
.svc p{font-size:14px;line-height:27px;margin-top:8px}
.svc a{display:inline-block;margin-top:10px;color:var(--white);font-size:14px;font-weight:700;text-decoration:underline}

/* sections */
.pale{background:var(--pale)}
.sec-h{font-size:37px;font-weight:600;color:var(--ink);text-transform:uppercase}
.rule{position:absolute;height:4px;width:84px;background:var(--blue)}
.photo-round{position:absolute;border-radius:50%;border:6px solid var(--blue)}
.body{font-size:16px;line-height:28px;color:#3c4452}

/* feature cards */
.feat{position:absolute;top:3095px;width:242px;height:335px;background:var(--white);border-radius:18px;box-shadow:0 4px 22px rgba(20,60,110,.10);text-align:center;padding:40px 14px 0}
.feat h3{font-size:25px;font-weight:600;color:var(--blue);line-height:28px;margin-top:26px}
.feat p{font-size:14px;line-height:27px;color:#444c58;margin-top:10px}
.feat.active{background:var(--blue)}
.feat.active h3,.feat.active p{color:var(--white)}

/* makers bar */
.makers{left:0;top:3510px;width:1200px;height:81px;display:flex}
.makers div{display:flex;align-items:center;justify-content:center;color:var(--white);font-family:"Exo 2",sans-serif;font-size:37px;font-weight:600;letter-spacing:1px}

/* form */
.field{position:absolute;border:1.5px solid #8b939e;border-radius:30px;font-size:16px;color:#3c4452;padding-left:22px;display:flex;align-items:center}

/* footer */
.foot-h{font-size:21px;font-weight:600;color:var(--blue);text-transform:uppercase}
.foot-list{list-style:none;font-size:16px;color:#3c4452;line-height:34px;margin-top:6px}
.addr{list-style:none;font-size:16px;color:#3c4452;margin-top:6px}
.addr li{display:flex;gap:16px;line-height:32px}
.addr .blue{color:var(--blue)}
.social{left:75px;top:4520px;display:flex;gap:22px}
.social span{width:20px;height:20px;border-radius:50%;background:var(--blue-dark)}
</style>
</head>
<body>

<!-- header -->
<a class="brand" href="https://lumavex.de/en/lumavex-english/" style="left:78px;top:40px">
  <span class="brand-dot"></span><span class="brand-name" style="font-size:30px">Lumavex</span>
</a>
<div class="abs toplinks">PICK-UP ORDER&nbsp; / &nbsp;ABOUT US&nbsp; / &nbsp;CONTACT US&nbsp; / &nbsp;<b>EN ⌄</b></div>
<div class="abs contact" style="left:632px;top:71px">
  <span class="icircle"><svg width="16" height="16" viewBox="0 0 24 24"><path fill="#fff" d="M6.6 10.8a15 15 0 0 0 6.6 6.6l2.2-2.2a1 1 0 0 1 1-.25 11.4 11.4 0 0 0 3.6.57 1 1 0 0 1 1 1V20a1 1 0 0 1-1 1A17 17 0 0 1 3 4a1 1 0 0 1 1-1h3.5a1 1 0 0 1 1 1c0 1.25.2 2.45.57 3.57a1 1 0 0 1-.25 1z"/></svg></span>
  <span>+49 4620 517 300-0</span>
</div>
<div class="abs contact" style="left:888px;top:71px">
  <span class="icircle"><svg width="16" height="16" viewBox="0 0 24 24"><path fill="#fff" d="M3 5h18v14H3z"/><path fill="none" stroke="#24405e" stroke-width="2" d="M3 6l9 7 9-7"/></svg></span>
  <span>info@lumavex.de</span>
</div>

<nav class="abs nav">
  <a style="left:85px">Home</a>
  <a style="left:162px">About Us</a>
  <a style="left:266px">Endoscope Repair</a>
  <a style="left:442px" href="https://lumavex.de/en/used-endoscopes/">Used Endoscopes</a>
  <a style="left:616px">Endoscopy Systems</a>
  <a style="left:807px">Endoscopy Accessories</a>
  <a style="left:1034px" href="https://lumavex.de/en/purchase/">Purchase</a>
</nav>

<!-- hero -->
<div class="abs hero" role="img" aria-label="Gloved hands holding the control section of a flexible endoscope"></div>
<div class="abs hero-inset" role="img" aria-label="Close-up of endoscope control wheels"></div>
<h1 class="abs hero-title">Lumavex</h1>
<div class="abs hero-sub display">Put Your Endoscope In<br>Reliable Hands!</div>
<a class="btn" style="left:75px;top:541px;width:215px;height:58px">Repair Request</a>
<svg class="abs" style="left:0;top:740px" width="1200" height="110" viewBox="0 0 1200 110" preserveAspectRatio="none">
  <path d="M0 50 C250 100 420 20 650 45 C880 70 1000 90 1200 10 L1200 110 L0 110Z" fill="var(--blue-dark)"/>
  <path d="M0 68 C250 110 430 35 660 58 C890 82 1020 100 1200 30 L1200 110 L0 110Z" fill="#fff"/>
</svg>

<!-- service cards -->
<div class="svc" style="left:75px;top:973px;width:345px;height:267px;background:var(--blue)">
  <svg width="54" height="54" viewBox="0 0 54 54" fill="none" stroke="#fff" stroke-width="2.5"><path d="M8 46L30 24M38 8a9 9 0 0 0-8 12l-3 3 4 4 3-3a9 9 0 0 0 12-8l-5 3-4-4zM10 8l10 10M8 14l6-6M32 32l12 12"/></svg>
  <h3>Repair</h3><h4>Endoscope repair service</h4>
  <p>Manufacturer-independent we repair and maintain endoscopes, individual components.</p>
  <a>Repair Request</a>
</div>
<div class="svc" style="left:404px;top:931px;width:392px;height:328px;background:var(--blue-dark);padding:48px 24px">
  <svg width="54" height="54" viewBox="0 0 54 54" fill="none" stroke="#fff" stroke-width="2.5"><path d="M6 22L22 6h22v22L28 44z"/><circle cx="36" cy="14" r="3"/><path d="M14 32l14-14"/></svg>
  <h3>Sale</h3><h4>Used endoscopes</h4>
  <p>Our regular stock includes refurbished gastroscopes, coloscopes, bronchoscopes cystoscopes and duodenoscopes .</p>
  <a href="https://lumavex.de/en/purchase/">Purchase Request</a>
</div>
<div class="svc" style="left:796px;top:973px;width:330px;height:267px;background:var(--blue)">
  <svg width="54" height="54" viewBox="0 0 54 54" fill="none" stroke="#fff" stroke-width="2.5"><rect x="6" y="6" width="42" height="30" rx="2"/><path d="M6 14h42M20 44h14M27 36v8M16 22h10v8H16z"/></svg>
  <h3>Purchase</h3><h4>Used endoscopes</h4>
  <p>We are very interested in buying your old endoscopes – even defective and dismantled.</p>
  <a>Sell Device</a>
</div>

<!-- about -->
<div class="abs pale" style="left:0;top:1334px;width:1200px;height:591px"></div>
<svg class="abs" style="left:0;top:1320px" width="1200" height="80" viewBox="0 0 1200 80" preserveAspectRatio="none">
  <path d="M0 0 C300 60 600 70 800 30 C980 -5 1100 20 1200 60 L1200 0Z" fill="var(--blue-dark)"/>
  <path d="M0 0 C300 45 600 55 800 18 C980 -12 1100 10 1200 45 L1200 0Z" fill="#fff"/>
</svg>
<h2 class="abs sec-h" style="left:75px;top:1460px">About Us</h2>
<div class="rule" style="left:75px;top:1522px"></div>
<p class="abs" style="left:75px;top:1552px;width:540px;font-size:18px;font-weight:600;line-height:28px;color:var(--blue)">Endoscope repairs and second hand endoscopes from Lumavex – cause the outcome matters!</p>
<p class="abs body" style="left:75px;top:1612px;width:530px">Lumavex is a privileged partner for the start-up facility or optimisation of existing healthcare facilities, doctor's offices and hospitals. The quality and reliability of our products and our offered service are our best advertisement!</p>
<a class="btn" style="left:75px;top:1750px;width:187px;height:56px">Read More</a>
<div class="photo-round" style="left:654px;top:1391px;width:478px;height:478px;background:linear-gradient(150deg,#eef1f5 0%,#aab4c0 50%,#3d4652 100%)" role="img" aria-label="Endoscope control body with angulation knobs"></div>
<svg class="abs" style="left:0;top:1855px" width="1200" height="80" viewBox="0 0 1200 80" preserveAspectRatio="none">
  <path d="M0 80 C200 20 450 20 650 40 C850 60 1050 40 1200 0 L1200 80Z" fill="var(--blue-dark)"/>
  <path d="M0 80 C220 35 460 35 660 52 C870 70 1060 55 1200 20 L1200 80Z" fill="#fff"/>
</svg>

<!-- future -->
<h2 class="abs sec-h" style="left:0;top:2000px;width:1200px;text-align:center">Your Future - Our Service</h2>
<p class="abs" style="left:150px;top:2088px;width:900px;text-align:center;font-size:19px;line-height:34px;color:#3c4452">Lumavex GmbH is specialised in the repair and sale of Optira, Vestan and Korima flexible medical endoscopes. As a service-oriented company, we are at your side with our knowledge and skills!</p>

<!-- faulty -->
<div class="abs pale" style="left:0;top:2275px;width:1200px;height:573px"></div>
<svg class="abs" style="left:0;top:2260px" width="1200" height="80" viewBox="0 0 1200 80" preserveAspectRatio="none">
  <path d="M0 70 C250 20 450 10 700 30 C950 50 1100 20 1200 0 L1200 0 L0 0Z" fill="#fff"/>
  <path d="M0 70 C250 20 450 10 700 30 C950 50 1100 20 1200 0 L1200 18 C1100 40 950 66 700 46 C450 28 250 36 0 84Z" fill="var(--blue-dark)"/>
</svg>
<div class="photo-round" style="left:68px;top:2330px;width:478px;height:478px;background:linear-gradient(140deg,#f4f5f7 0%,#bfc5cd 45%,#30353d 100%)" role="img" aria-label="Endoscope control body lying on a white surface"></div>
<h2 class="abs sec-h" style="left:612px;top:2395px">Faulty Endoscope?</h2>
<div class="rule" style="left:615px;top:2460px"></div>
<p class="abs body" style="left:615px;top:2483px;width:520px;font-size:15.5px">We want to help you so that there are least possible restrictions in your doctor's office or hospital!</p>
<p class="abs body" style="left:615px;top:2553px;width:520px;font-size:15.5px">Use the following form to place a pick-up order for your defective device. We will inform you immediately whether we will come to you for error analysis or whether your device needs to be picked up by a courier service.</p>
<a class="btn" style="left:615px;top:2688px;width:187px;height:55px">Pick-up Order</a>
<svg class="abs" style="left:0;top:2790px" width="1200" height="80" viewBox="0 0 1200 80" preserveAspectRatio="none">
  <path d="M0 10 C200 50 450 60 700 40 C950 20 1100 30 1200 50 L1200 80 L0 80Z" fill="var(--blue-dark)"/>
  <path d="M0 28 C200 62 450 72 700 54 C950 36 1100 44 1200 62 L1200 80 L0 80Z" fill="#fff"/>
</svg>

<!-- decision -->
<h2 class="abs sec-h" style="left:0;top:2928px;width:1200px;text-align:center;line-height:46px">Lumavex GmbH, Your Decision<br>For Your Future</h2>
<div class="rule" style="left:558px;top:3037px"></div>
<svg class="abs" style="left:42px;top:3250px" width="16" height="26" viewBox="0 0 16 26" fill="none" stroke="#555" stroke-width="2"><path d="M14 2L3 13l11 11"/></svg>
<svg class="abs" style="left:1140px;top:3250px" width="16" height="26" viewBox="0 0 16 26" fill="none" stroke="#555" stroke-width="2"><path d="M2 2l11 11L2 24"/></svg>

<div class="feat" style="left:75px">
  <svg width="56" height="56" viewBox="0 0 56 56" fill="none" stroke="var(--blue)" stroke-width="5"><circle cx="28" cy="28" r="24"/><path d="M28 14v15l9 5"/></svg>
  <h3>Fast Repairs</h3>
  <p>Keep potential disruptions in your doctor's office or in your hospital at minimum as a result of optimized processes.</p>
</div>
<div class="feat" style="left:345px">
  <svg width="56" height="56" viewBox="0 0 56 56"><path fill="var(--blue)" d="M44 4a12 12 0 0 0-14 15L6 43a5 5 0 0 0 7 7l24-24A12 12 0 0 0 52 12l-7 7-8-2-2-8 7-7z"/></svg>
  <h3>On-Site Service</h3>
  <p>We will gladly pay you a visit to to carry out analysis and repairs on site. Due to our many years of experience.</p>
</div>
<div class="feat active" style="left:615px">
  <svg width="72" height="56" viewBox="0 0 72 56" fill="#fff"><circle cx="24" cy="32" r="16"/><circle cx="24" cy="32" r="6" fill="var(--blue)"/><circle cx="54" cy="16" r="10"/><circle cx="54" cy="16" r="4" fill="var(--blue)"/><circle cx="54" cy="44" r="8"/><circle cx="54" cy="44" r="3" fill="var(--blue)"/></svg>
  <h3>Loan Equipment Service</h3>
  <p>Use our service of high-quality loan devices during the downtime of your defective endoscope.</p>
</div>
<div class="feat" style="left:885px">
  <svg width="40" height="56" viewBox="0 0 40 56"><text x="20" y="50" text-anchor="middle" font-family="Montserrat,sans-serif" font-size="56" font-weight="700" fill="var(--blue)">$</text></svg>
  <h3>Highly Cost Efficient</h3>
  <p>Benefit from our first class recommendations and implementation by our experienced staff.</p>
</div>

<!-- makers -->
<div class="abs makers">
  <div style="width:404px;background:var(--blue-dark)">OPTIRA</div>
  <div style="width:392px;background:var(--blue)">VESTAN</div>
  <div style="width:404px;background:var(--blue-dark)">KORIMA</div>
</div>

<!-- form -->
<h2 class="abs sec-h" style="left:0;top:3645px;width:1200px;text-align:center">How Can We Help You?</h2>
<div class="field" style="left:254px;top:3761px;width:332px;height:56px">Name</div>
<div class="field" style="left:616px;top:3761px;width:332px;height:56px">Email Address</div>
<div class="field" style="left:254px;top:3835px;width:332px;height:56px">Phone No</div>
<div class="field" style="left:616px;top:3835px;width:332px;height:56px">Subject</div>
<div class="field" style="left:254px;top:3910px;width:694px;height:129px;border-radius:16px;align-items:flex-start;padding-top:18px">Message</div>
<a class="btn" style="left:496px;top:4062px;width:208px;height:60px;font-size:18px">Submit</a>

<!-- footer -->
<div class="abs pale" style="left:0;top:4200px;width:1200px;height:415px"></div>
<svg class="abs" style="left:0;top:4165px" width="1200" height="90" viewBox="0 0 1200 90" preserveAspectRatio="none">
  <path d="M0 60 C200 30 450 10 700 30 C950 50 1080 30 1200 5 L1200 90 L0 90Z" fill="var(--blue-dark)"/>
  <path d="M0 78 C220 46 460 26 710 46 C960 66 1090 48 1200 24 L1200 90 L0 90Z" fill="var(--pale)"/>
</svg>
<a class="brand" style="left:90px;top:4340px">
  <span class="brand-dot"></span><span class="brand-name" style="font-size:28px">Lumavex</span>
</a>
<p class="abs" style="left:75px;top:4450px;font-size:16px;line-height:27px;color:#3c4452">© 2022 Lumavex GmbH<br>All Right Reserved</p>
<div class="abs social"><span></span><span></span><span></span><span></span><span></span></div>

<div class="abs" style="left:346px;top:4290px">
  <div class="foot-h">Site Map</div>
  <ul class="foot-list"><li>Home</li><li>Endoscope Repair</li><li>Used Endoscopes</li><li>Endoscopy Systems</li><li>Endoscopy Accessories</li><li>Purchase</li><li>Contact Us</li></ul>
</div>
<div class="abs" style="left:601px;top:4290px">
  <div class="foot-h">Quick Links</div>
  <ul class="foot-list"><li>Informations</li><li>About Us</li><li>Contact Us</li><li>Tos</li><li>Copyrights</li><li>Privacy Policy</li></ul>
</div>
<div class="abs" style="left:836px;top:4290px;width:340px">
  <div class="foot-h">Address Info</div>
  <div style="font-size:16px;font-weight:600;color:var(--blue);margin-top:6px">Lumavex GmbH</div>
  <ul class="addr">
    <li><svg width="18" height="16" viewBox="0 0 18 16" style="margin-top:8px"><path fill="var(--blue-dark)" d="M0 2l6-2 6 2 6-2v14l-6 2-6-2-6 2z"/></svg><span style="line-height:26px">Lindenweg 12<br>21470 Talbruck Germany</span></li>
    <li><svg width="18" height="18" viewBox="0 0 24 24" style="margin-top:7px"><path fill="var(--blue-dark)" d="M6.6 10.8a15 15 0 0 0 6.6 6.6l2.2-2.2a1 1 0 0 1 1-.25 11.4 11.4 0 0 0 3.6.57 1 1 0 0 1 1 1V20a1 1 0 0 1-1 1A17 17 0 0 1 3 4a1 1 0 0 1 1-1h3.5a1 1 0 0 1 1 1c0 1.25.2 2.45.57 3.57a1 1 0 0 1-.25 1z"/></svg><span class="blue">+49 4620 517 300-0</span></li>
    <li><svg width="18" height="18" viewBox="0 0 18 18" style="margin-top:7px"><rect x="1" y="6" width="16" height="11" fill="var(--blue-dark)"/><rect x="4" y="1" width="10" height="6" fill="none" stroke="var(--blue-dark)" stroke-width="2"/></svg><span class="blue">+49 4620 517 300-1</span></li>
    <li><svg width="18" height="14" viewBox="0 0 18 14" style="margin-top:9px"><rect width="18" height="14" fill="var(--blue-dark)"/><path d="M0 1l9 7 9-7" fill="none" stroke="#fff" stroke-width="1.5"/></svg><span class="blue">info@lumavex.de</span></li>
  </ul>
</div>

</body>
</html>
```